Automotive Business Card Design

I would just like a automotive themed card. nothing too extravagant, but catchy.

needs to say something about doing roadside assistance,mobile repairs, Diesel repairs, and Fleet maintenance

it can be single sided or double sided. no preference there.

Industry/Entity Type

Automotive

Contact Information for Business Card

Dean Marlowe
phone 534 861 2093
Name: Brightpath Automotive & Diesel Repair

```html
<!DOCTYPE html>
<html lang="en">
<head>
<meta charset="utf-8">
<title>Brightpath Automotive &amp; Diesel Repair – Business Card</title>
<link rel="stylesheet" href="https://fonts.googleapis.com/css2?family=Aldrich&display=swap">
<style>
  :root {
    --backdrop: #8e8e8e;
    --card: #f7f7f7;
    --ink: #2b2b2b;
    --ink-soft: #555555;
    --band-dark: #262626;
    --blue-deep: #1b8fd6;
    --blue-light: #4fc3dc;
    --edge: #d9d9d9;
  }
  * { box-sizing: border-box; margin: 0; padding: 0; }
  html, body { width: 1200px; height: 895px; overflow: hidden; }
  body {
    background: var(--backdrop);
    font-family: "Aldrich", "Arial", sans-serif;
    color: var(--ink);
    position: relative;
  }
  .card {
    position: absolute;
    width: 540px;
    height: 310px;
    background: var(--card);
    box-shadow: 0 10px 24px rgba(0,0,0,0.28);
    overflow: hidden;
  }
  .card--back  { left: 610px; top: 120px; }
  .card--front { left: 50px;  top: 450px; }
  .card svg.shapes { position: absolute; inset: 0; }

  .brand {
    position: absolute;
    display: flex;
    align-items: center;
    gap: 10px;
    color: var(--ink);
    white-space: nowrap;
    letter-spacing: 0.5px;
  }
  .brand__dot {
    width: 14px; height: 14px; border-radius: 50%;
    background: var(--blue-deep);
    flex: none;
  }
  .card--back .brand { left: 50%; top: 143px; transform: translateX(-50%); font-size: 19px; }
  .card--front .brand { left: 22px; top: 20px; font-size: 15px; gap: 8px; }
  .card--front .brand__dot { width: 12px; height: 12px; }

  .person { position: absolute; right: 24px; top: 52px; text-align: right; }
  .person__name { font-size: 19px; letter-spacing: 1.5px; text-transform: uppercase; }
  .person__role { font-size: 8px; letter-spacing: 1px; text-transform: uppercase; color: var(--ink-soft); margin-top: 5px; }

  .contact { position: absolute; top: 166px; font-size: 11px; line-height: 17px; color: var(--ink); letter-spacing: 0.3px; white-space: nowrap; }
  .contact--web { left: 20px; font-size: 10.5px; }
  .contact--address { left: 190px; }
  .contact--phone { left: 392px; font-size: 13px; letter-spacing: 1px; }

  .services {
    position: absolute;
    left: 0; right: 0; top: 222px;
    text-align: center;
    font-size: 10px;
    letter-spacing: 0.8px;
    text-transform: uppercase;
    color: var(--ink-soft);
    white-space: nowrap;
  }
</style>
</head>
<body>

  <section class="card card--back" aria-label="Card back">
    <svg class="shapes" width="540" height="310" viewBox="0 0 540 310" aria-hidden="true">
      <defs>
        <linearGradient id="blueBandBack" x1="0" y1="0" x2="1" y2="0">
          <stop offset="0" stop-color="#1b8fd6"/>
          <stop offset="0.5" stop-color="#4fc3dc"/>
          <stop offset="1" stop-color="#1b8fd6"/>
        </linearGradient>
      </defs>
      <rect x="0" y="0" width="540" height="44" fill="url(#blueBandBack)"/>
      <rect x="0" y="266" width="540" height="44" fill="url(#blueBandBack)"/>
      <rect x="0" y="44" width="540" height="4" fill="#d9d9d9"/>
      <rect x="0" y="262" width="540" height="4" fill="#d9d9d9"/>
      <polygon points="176,0 186,0 198,22 186,44 176,44 188,22" fill="#f7f7f7"/>
      <polygon points="356,0 366,0 378,22 366,44 356,44 368,22" fill="#f7f7f7"/>
      <polygon points="176,266 186,266 198,288 186,310 176,310 188,288" fill="#f7f7f7"/>
      <polygon points="356,266 366,266 378,288 366,310 356,310 368,288" fill="#f7f7f7"/>
    </svg>
    <div class="brand"><span class="brand__dot"></span>Brightpath Automotive &amp; Diesel Repair</div>
  </section>

  <section class="card card--front" aria-label="Card front">
    <svg class="shapes" width="540" height="310" viewBox="0 0 540 310" aria-hidden="true">
      <defs>
        <linearGradient id="blueBandFront" x1="0" y1="0" x2="1" y2="0">
          <stop offset="0" stop-color="#1b8fd6"/>
          <stop offset="0.5" stop-color="#4fc3dc"/>
          <stop offset="1" stop-color="#1b8fd6"/>
        </linearGradient>
      </defs>
      <rect x="0" y="100" width="540" height="42" fill="#262626"/>
      <polygon points="172,100 182,100 194,121 182,142 172,142 184,121" fill="#f7f7f7"/>
      <polygon points="354,100 364,100 376,121 364,142 354,142 366,121" fill="#f7f7f7"/>
      <g fill="none" stroke="#f7f7f7" stroke-width="1.6">
        <circle cx="40" cy="121" r="10"/>
        <ellipse cx="40" cy="121" rx="4.5" ry="10"/>
        <line x1="30" y1="121" x2="50" y2="121"/>
        <line x1="32" y1="115" x2="48" y2="115"/>
        <line x1="32" y1="127" x2="48" y2="127"/>
      </g>
      <path d="M268 109 a8 8 0 0 1 8 8 c0 6 -8 15 -8 15 s-8 -9 -8 -15 a8 8 0 0 1 8 -8 z" fill="#f7f7f7"/>
      <circle cx="268" cy="117" r="3" fill="#262626"/>
      <rect x="446" y="108" width="14" height="25" rx="2.5" fill="none" stroke="#f7f7f7" stroke-width="1.6"/>
      <line x1="449" y1="112" x2="457" y2="112" stroke="#f7f7f7" stroke-width="1"/>
      <circle cx="453" cy="129" r="1.3" fill="#f7f7f7"/>
      <rect x="0" y="250" width="540" height="4" fill="#d9d9d9"/>
      <rect x="0" y="254" width="540" height="56" fill="url(#blueBandFront)"/>
    </svg>

    <div class="brand"><span class="brand__dot"></span>Brightpath Automotive &amp; Diesel Repair</div>

    <div class="person">
      <p class="person__name">Dean Marlowe</p>
      <p class="person__role">Graphics Designer</p>
    </div>

    <p class="contact contact--web">dean@brightpathauto.com<br>www.brightpathauto.com</p>
    <p class="contact contact--address">214 Harbor Street Suite 6<br>Marlow Park</p>
    <p class="contact contact--phone">534 861 2093<br>534 861 2093</p>

    <p class="services">Roadside Assistance · Mobile Repairs · Diesel Repairs · Fleet Maintenance</p>
  </section>

</body>
</html>
```